Branding product image: VELMOT (Golden Papaya) in Plastic Cup (Ready to Eat)

The product is sliced Fruit in Light syrup
Flavour: VELMOT (Golden Papaya)
The temporary product name: VELMOT
I want the product design to be something 'fun', 'natural', and 'colourful'
The design concept could be anything depends on your imagination, but it must be eye catchy and attractive.
Basically, I want you to be creative in designing the logo and the overall graphic design for the label.
The measurement is 20 cm (Length) x 6,5 cm (Height)
The target customers are young and health conscious audiences (10 years - 65 years old).
Create something different. Something extraordinary.
Brief summary about the fruit:
This fruit only grows in certain part of the world. It grows in mountain area that is in tropical climate. The fruit flesh has a yellowish-golden color. It has an extraordinary taste (unlike normal papaya) and it suits very well with any dishes from cold appetizer, white/ red meat, desserts, and cocktails.
I need a packaging design for Fruit Cup productThe product is sliced Fruit in Light syrup.There will be various flavours i.e. apple, lychee, peach, papaya, etc.However, you may design the product using one sample flavour (i.e. papaya) first, as the designs of other flavours could be adjusted afterwards.The temporary product name is: RICCANAI want the product design to be something 'fun', 'natural', and 'colourful'.The design concept could be anything depends on your imagination. Basically, I want you to be creative in designing the logo and the overall graphic design for the label. - Create something different. Something extraordinary -Additional:The measurement is 20cm (Length) x 5cm (Height).The target customers are young audiences (10 years - 35 years old).The product design must stand out in the supermarket shelf.It must be eye catchy and attractive.Thank you,Jordan-PLEASE REFER TO DESIGN SAMPLE ATTACHED TO HAVE A BETTER UNDERSTANDING FOR THE PRODUCT CONCEPT- Added Wednesday, September 17, 2014
Project Deadline Extended Reason: Haven't found a good design. Added Friday, September 19, 2014
Project Deadline Extended Reason: Need more time for designers to finalize and perfect the design.Thank you,Jordan Added Monday, September 29, 2014
Project Deadline Extended Reason: I haven't found a great design yet. Added Tuesday, February 24, 2015
Reason: Getting better designs now. Still Open to new ideas while refining the latest designs from some designers.
Please do your best in submitting other great designs!

```html
<!DOCTYPE html>
<html lang="en">
<head>
<meta charset="utf-8">
<title>DOSUVEL – Apple Sliced Label</title>
<link rel="stylesheet" href="https://fonts.googleapis.com/css2?family=Montserrat:wght@400&family=Shadows+Into+Light&family=Luckiest+Guy&family=Open+Sans:wght@400&display=swap">
<style>
  :root {
    --cream: #f9f6c4;
    --band: #d8aa6c;
    --band-line: #f3dfbe;
    --ink: #1d1d1b;
    --red: #e3202a;
    --cloth-light: #d6ea9f;
    --cloth-mid: #bddb75;
    --cloth-deep: #a6cc57;
    --trim: #ffffff;
    --trim-shade: #efefe4;
    --mascot-light: #c9e26a;
    --mascot-mid: #9cc83a;
    --mascot-deep: #7fae2c;
  }
  html, body {
    margin: 0;
    padding: 0;
    overflow: hidden;
    background: #ffffff;
  }
  .label {
    position: relative;
    width: 1200px;
    height: 572px;
    overflow: hidden;
    background: var(--cream);
  }
  .brand-band {
    position: absolute;
    left: 0;
    top: 28px;
    width: 1170px;
    height: 70px;
    background: var(--band);
  }
  .brand-band__rule {
    position: absolute;
    top: 34px;
    height: 2px;
    background: var(--band-line);
  }
  .brand-band__rule--left { left: 0; width: 360px; }
  .brand-band__rule--right { right: 0; width: 350px; }
  .brand-name {
    position: absolute;
    left: 0;
    right: 0;
    top: 0;
    height: 70px;
    margin: 0;
    line-height: 70px;
    text-align: center;
    font-family: "Montserrat", sans-serif;
    font-weight: 400;
    font-size: 44px;
    letter-spacing: 22px;
    padding-left: 22px;
    color: #ffffff;
  }
  .tagline {
    position: absolute;
    left: 0;
    right: 0;
    top: 140px;
    margin: 0;
    text-align: center;
    font-family: "Shadows Into Light", cursive;
    font-size: 66px;
    line-height: 90px;
    color: var(--ink);
  }
  .tablecloth {
    position: absolute;
    left: 0;
    top: 340px;
    width: 1200px;
    height: 232px;
    background: linear-gradient(180deg, var(--cloth-light) 0%, var(--cloth-mid) 55%, var(--cloth-deep) 100%);
  }
  .lace-trim {
    position: absolute;
    left: 0;
    top: 302px;
    width: 1200px;
    height: 44px;
    background: linear-gradient(180deg, var(--trim) 0%, var(--trim-shade) 100%);
    box-shadow: 0 5px 8px rgba(0,0,0,0.12);
  }
  .mascot {
    position: absolute;
    left: 78px;
    top: 234px;
    width: 455px;
    height: 326px;
    border-radius: 48% 52% 46% 54% / 50% 50% 50% 50%;
    background: radial-gradient(ellipse at 58% 50%, var(--mascot-light) 0%, var(--mascot-mid) 55%, var(--mascot-deep) 100%);
    opacity: 0.92;
  }
  .product-name {
    position: absolute;
    left: 560px;
    top: 372px;
    margin: 0;
    font-family: "Luckiest Guy", "Impact", sans-serif;
    font-weight: 400;
    font-size: 58px;
    line-height: 66px;
    color: var(--red);
    -webkit-text-stroke: 8px var(--ink);
    paint-order: stroke fill;
    letter-spacing: 1px;
    transform: rotate(-2deg);
    white-space: nowrap;
  }
  .product-variant {
    position: absolute;
    left: 630px;
    top: 452px;
    margin: 0;
    font-family: "Open Sans", sans-serif;
    font-size: 31px;
    line-height: 40px;
    color: var(--ink);
    white-space: nowrap;
  }
</style>
</head>
<body>
<main class="label">
  <div class="brand-band">
    <span class="brand-band__rule brand-band__rule--left"></span>
    <span class="brand-band__rule brand-band__rule--right"></span>
    <h1 class="brand-name">DOSUVEL</h1>
  </div>

  <p class="tagline">Eat Me If You Dare!!!</p>

  <div class="tablecloth" role="img" aria-label="Green and white gingham tablecloth pattern"></div>
  <div class="lace-trim" role="img" aria-label="White scalloped lace trim along the tablecloth edge"></div>

  <div class="mascot" role="img" aria-label="Illustration of a laughing, winking green apple mascot with two large leaves behind it"></div>

  <h2 class="product-name">APPLE SLICED</h2>
  <p class="product-variant">in Light syrup</p>
</main>
</body>
</html>
```